Business card design for Brivo Engineering Tandem

We need a new business card design along with all the necessary to place an order. The company is Brivo Engineering Tandem and we recently updated our logo.

```html
<!DOCTYPE html>
<html lang="en">
<head>
<meta charset="utf-8">
<title>Brivo Engineering Tandem – Business Card</title>
<link href="https://fonts.googleapis.com/css2?family=Kanit:wght@400;500;600&display=swap" rel="stylesheet">
<style>
  :root {
    --backdrop: #3b3b3d;
    --card: #f1f1f1;
    --brand-yellow: #d5b11f;
    --brand-grey: #7d7d7d;
    --ink: #1d1d1d;
  }
  * { box-sizing: border-box; margin: 0; padding: 0; }
  html, body { width: 1200px; height: 1059px; overflow: hidden; }
  body {
    background: var(--backdrop);
    font-family: "Kanit", sans-serif;
    position: relative;
  }
  .card {
    position: absolute;
    width: 690px;
    height: 394px;
    background: var(--card);
    border-radius: 22px;
    overflow: hidden;
  }
  .card--front { left: 256px; top: 100px; }
  .card--back { left: 254px; top: 536px; }

  .wordmark {
    position: absolute;
    display: flex;
    align-items: center;
    font-weight: 500;
    color: var(--brand-grey);
    text-transform: uppercase;
    white-space: nowrap;
  }
  .wordmark__square {
    background: var(--brand-yellow);
    flex: none;
  }
  .card--front .wordmark { left: 28px; top: 50px; font-size: 29px; gap: 14px; }
  .card--front .wordmark__square { width: 30px; height: 30px; }
  .card--back .wordmark {
    left: 0; right: 0; top: 168px;
    justify-content: center;
    font-size: 40px; gap: 18px;
  }
  .card--back .wordmark__square { width: 42px; height: 42px; }

  .accent-bar {
    position: absolute;
    left: 0; top: 155px;
    width: 13px; height: 52px;
    background: var(--brand-yellow);
  }
  .contact {
    position: absolute;
    left: 28px; top: 148px;
    color: var(--ink);
  }
  .contact__name {
    font-weight: 600;
    font-size: 32px;
    line-height: 38px;
    color: var(--brand-yellow);
    letter-spacing: 0.2px;
  }
  .contact__role {
    font-size: 17px;
    line-height: 24px;
    margin-top: 0;
  }
  .contact__address {
    font-size: 17px;
    line-height: 27px;
    margin-top: 16px;
  }
  .contact__lines {
    list-style: none;
    margin-top: 12px;
  }
  .contact__lines li {
    display: flex;
    align-items: center;
    gap: 8px;
    font-size: 17px;
    line-height: 27px;
  }
  .contact__lines svg { width: 15px; height: 15px; fill: var(--brand-yellow); flex: none; }
</style>
</head>
<body>
  <section class="card card--front" aria-label="Business card front">
    <div class="wordmark"><span class="wordmark__square"></span>Brivo Engineering Tandem</div>
    <span class="accent-bar"></span>
    <div class="contact">
      <h1 class="contact__name">DANIEL HART</h1>
      <p class="contact__role">Managing Director</p>
      <p class="contact__address">Brivo Engineering Tandem<br>24 Corran Road, Kettleby KT4 2LP</p>
      <ul class="contact__lines">
        <li>
          <svg viewBox="0 0 16 16" aria-hidden="true"><path d="M1 6c0-2 3-3.5 7-3.5S15 4 15 6v1.5h-3.5V6h-7v1.5H1z"/><path d="M3.5 8.5h9l1.5 5H2z"/></svg>
          01632 960418
        </li>
        <li>
          <svg viewBox="0 0 16 16" aria-hidden="true"><path d="M1 3.5h14v1L8 9 1 4.5z"/><path d="M1 6l7 4.5L15 6v6.5H1z"/></svg>
          sales@brivoengineering.co.uk
        </li>
        <li>
          <svg viewBox="0 0 16 16" aria-hidden="true"><circle cx="8" cy="8" r="7"/><path d="M4 4.5c1.5 0 2 1 3 1s1 1.5 0 2-2 .5-2 2-1 1.5-1.5 1" fill="none" stroke="#f1f1f1" stroke-width="1.2"/></svg>
          www.brivoengineering.co.uk
        </li>
      </ul>
    </div>
  </section>

  <section class="card card--back" aria-label="Business card back">
    <div class="wordmark"><span class="wordmark__square"></span>Brivo Engineering Tandem</div>
  </section>
</body>
</html>
```